Website Design for a holiday home letting busines

We require a redesign of our present website www.pinebrookstays.com. We want the website to stand out and look professional and clean to make holiday hunters want to book a caravan or lodge holiday with us. Our logo is red however we DO NOT want the website to be red. We want a natural colour scheme.

The final design should communicate that we are a professional company to book with.

On the home page we require;
Overview of company
Photo
Search box for holiday (check in)
Late Deals
Reviews
News

We would like the following pages designed; home page, available dates page, caravans page, content page.

The website should be responsive for smart phones. One website I do like is http://www.verdoliso.be/nl/

Target Market(s)

Families

Industry/Entity Type

Travel

Number of Pages Required

5+ page

Font styles to use
Serif

Requirements
Must have
• The project must be responsive for mobile phones and tablets.
• Ability to search for holiday home holidays
• We want a natural colour scheme.
Nice to have
• A style we like is http://www.verdoliso.be/nl/
Should not have
• Do not use red as a colour for the website. Our logo is red so this is the only time we want this used.

```html
<!DOCTYPE html>
<html lang="en">
<head>
<meta charset="utf-8">
<title>Pinebrook Stays – Ashford Lodge</title>
<link href="https://fonts.googleapis.com/css2?family=Open+Sans:wght@400;600;700;800&display=swap" rel="stylesheet">
<style>
:root{
  --blue:#1f73b7;
  --blue-dark:#17578c;
  --navy:#143d61;
  --green:#8cb83c;
  --green-dark:#76a02c;
  --grey-bg:#e9ecee;
  --line:#dde2e6;
  --text:#4a5560;
  --muted:#8a949c;
  --white:#ffffff;
}
*{box-sizing:border-box;margin:0;padding:0}
html,body{width:1200px;height:3264px;overflow:hidden}
body{font-family:"Open Sans",Arial,sans-serif;color:var(--text);background:var(--grey-bg);position:relative;font-size:12px;line-height:1.55}
.abs{position:absolute}
ul{list-style:none}

/* header */
.site-header{left:0;top:0;width:1200px;height:84px;background:var(--white)}
.brand{left:160px;top:24px;display:flex;align-items:center;gap:10px;font-size:22px;font-weight:700;color:var(--blue-dark)}
.brand-dot{width:30px;height:30px;border-radius:50%;background:var(--blue)}
.brand small{display:block;font-size:10px;font-weight:400;color:var(--muted)}
.call{left:760px;top:24px;text-align:right;width:150px;font-size:10px;color:var(--muted)}
.call strong{display:block;font-size:16px;color:var(--blue-dark)}
.questions{left:930px;top:22px;width:110px;height:40px;border-radius:4px;background:var(--green);color:var(--white);font-weight:700;font-size:13px;display:flex;align-items:center;justify-content:center}

.hero{left:0;top:84px;width:1200px;height:156px;background:linear-gradient(180deg,#c9d6df 0%,#e4e9ec 100%)}
.main-nav{left:0;top:84px;width:1200px;height:38px;background:rgba(23,87,140,.9)}
.main-nav ul{position:absolute;left:160px;top:0;display:flex;height:38px}
.main-nav li{color:var(--white);font-size:11px;font-weight:600;text-transform:uppercase;padding:0 16px;line-height:38px}
.main-nav li.active{background:var(--green)}

/* left column */
.title-bar{left:60px;top:252px;width:780px;height:40px;background:var(--green);color:var(--white);font-size:18px;font-weight:700;padding:0 18px;line-height:40px}
.gallery-main{left:60px;top:292px;width:780px;height:270px;background:linear-gradient(135deg,#b89a78,#e6d6c0 55%,#8b7a66)}
.thumbs{left:60px;top:562px;width:780px;height:86px;background:var(--navy);display:flex;gap:8px;padding:8px 40px}
.thumb{flex:1;background:linear-gradient(135deg,#a98d6e,#dcc9b0)}

.panel{background:var(--white)}
.details{left:60px;top:672px;width:780px;height:380px}
.sec-head{height:36px;background:var(--blue);color:var(--white);font-size:16px;font-weight:700;padding:0 16px;line-height:36px}
.details-text{left:0;top:0;width:390px;height:380px}
.details-text p{padding:14px 16px 0;font-size:11px}
.spec{left:410px;top:0;width:200px}
.spec h4,.spec-values h4{height:36px;font-size:11px;font-weight:700;padding:4px 10px;line-height:14px}
.spec h4{color:var(--blue)}
.spec li,.spec-values li{height:28px;font-size:11px;line-height:28px;padding:0 10px;border-bottom:1px solid var(--line);display:flex;align-items:center;gap:8px}
.spec svg{flex:none}
.spec-values{left:620px;top:0;width:160px}
.spec-values h4{background:var(--green);color:var(--white);text-align:center}
.spec-values li{justify-content:center;background:#f4f7ee}

.booking{left:60px;top:1072px;width:780px;height:660px}
.pay-box{margin:18px 16px 16px;width:260px;height:50px;border:1px solid var(--line);display:flex;align-items:center;gap:10px;padding:0 14px;font-size:20px;font-weight:700;color:var(--navy)}
.pay-box span{width:24px;height:24px;background:var(--navy)}
.booking p{padding:0 16px 16px;font-size:12px;line-height:1.8}
.booking p strong{color:var(--navy)}
.booking a{color:var(--blue);font-weight:600}

/* sidebar */
.availability{left:860px;top:252px;width:280px;height:1310px;background:var(--blue);color:var(--white)}
.side-head{height:44px;font-size:18px;font-weight:700;padding:0 16px;line-height:44px}
.availability p{padding:4px 16px 12px;font-size:11px}
.tabs{display:flex;margin:0 16px 10px}
.tabs div{flex:1;text-align:center;height:36px;line-height:36px;font-weight:700;font-size:13px;background:var(--navy)}
.tabs div.on{background:var(--green)}
.dates{margin:0 16px}
.dates li{height:41px;display:flex;justify-content:space-between;align-items:center;padding:0 10px;font-size:10.5px;border-bottom:1px solid rgba(255,255,255,.15)}
.dates li:nth-child(odd){background:rgba(255,255,255,.08)}
.dates li.dark{background:var(--navy)}
.dates li.dark:nth-child(odd){background:#1a4a73}
.dates b{font-weight:700}

.reviews{left:860px;top:1582px;width:280px;height:170px}
.reviews .side-head{background:var(--blue);color:var(--white)}
.reviews h5{padding:12px 16px 0;font-size:12px;color:var(--navy)}
.reviews em{display:block;padding:0 16px;font-size:10px;color:var(--muted);font-style:normal}
.reviews p{padding:6px 16px;font-size:10.5px}

/* features */
.features{left:0;top:1780px;width:1200px;height:350px;background:var(--blue);color:var(--white)}
.features h2{text-align:center;font-size:26px;font-weight:800;letter-spacing:2px;margin-top:40px}
.feat-cols{position:absolute;left:160px;top:110px;width:880px;display:flex}
.feat-cols ul{flex:1}
.feat-cols li{display:flex;align-items:center;gap:8px;font-size:11.5px;height:22px}

/* properties */
.cards{left:160px;top:2170px;width:880px;display:grid;grid-template-columns:repeat(4,220px);grid-auto-rows:210px}
.card-photo{background:linear-gradient(135deg,#9c8567,#d8c6ad 60%,#7e6d5a)}
.card-text{background:var(--white);padding:22px 18px}
.card-text h3{font-size:15px;font-weight:800;color:var(--navy);text-transform:uppercase}
.card-text p{font-size:10.5px;margin:10px 0 14px}
.card-btn{display:inline-block;background:var(--green);color:var(--white);font-size:10px;font-weight:700;padding:5px 14px}
.stars{margin-top:14px;display:flex;gap:3px}
.view-all{left:540px;top:2622px;width:120px;height:38px;background:var(--blue);color:var(--white);font-weight:700;font-size:12px;text-align:center;line-height:38px;text-transform:uppercase}

/* footer */
.site-footer{left:0;top:2720px;width:1200px;height:470px;background:var(--blue);color:var(--white)}
.foot-col{top:50px}
.foot-col h4{font-size:17px;font-weight:800;text-transform:uppercase;margin-bottom:16px}
.foot-col p{font-size:11px;margin-bottom:12px}
.input{width:240px;height:34px;background:var(--white);margin-bottom:12px}
.subscribe{width:110px;height:32px;background:var(--green);font-weight:700;font-size:11px;text-align:center;line-height:32px;text-transform:uppercase}
.sitemap{display:grid;grid-template-columns:130px 130px;row-gap:10px;font-size:11px}
.bottom-bar{left:0;top:3190px;width:1200px;height:74px;background:var(--navy);color:#c4d3df;font-size:10.5px}
.bottom-bar .copy{position:absolute;left:160px;top:28px}
.social{position:absolute;right:160px;top:22px;display:flex;align-items:center;gap:10px}
.social i{width:26px;height:26px;border-radius:50%;background:var(--blue)}
</style>
</head>
<body>

<header class="site-header abs">
  <div class="brand abs"><span class="brand-dot"></span><div>Pinebrook Stays<small>Holiday lodges &amp; caravans</small></div></div>
  <div class="call abs">Call us today<strong>0800 555 0142</strong></div>
  <div class="questions abs">Questions?</div>
</header>

<div class="hero abs" role="img" aria-label="Holiday park scenery banner"></div>
<nav class="main-nav abs">
  <ul>
    <li class="active">Home</li><li>Beds</li><li>Reviews</li><li>Lodges &amp; Caravans</li><li>Payment Plans</li><li>Information Centre</li><li>Latest Deals</li><li>Contact Us</li>
  </ul>
</nav>

<h1 class="title-bar abs">Ashford Lodge</h1>
<div class="gallery-main abs" role="img" aria-label="Lodge living room interior"></div>
<div class="thumbs abs">
  <div class="thumb" role="img" aria-label="Lounge"></div>
  <div class="thumb" role="img" aria-label="Kitchen"></div>
  <div class="thumb" role="img" aria-label="Bedroom"></div>
  <div class="thumb" role="img" aria-label="Bathroom"></div>
  <div class="thumb" role="img" aria-label="Dining area"></div>
  <div class="thumb" role="img" aria-label="Decking"></div>
</div>

<section class="details panel abs">
  <div class="details-text abs">
    <div class="sec-head">Details</div>
    <p>Our luxury Ashford Lodge sleeps up to six guests in a bright open-plan space with a fully fitted kitchen, cosy lounge and dining area overlooking the woodland.</p>
    <p>The master bedroom has its own en-suite shower and vanity, while the two further bedrooms share a modern family bathroom close by.</p>
    <p>Outside there is a large wrap-around deck with seating, perfect for warm evenings. Parking is right beside the lodge.</p>
    <p>Bed linen, towels, heating and Wi-Fi are all included, so you can simply arrive, unpack and relax with the family.</p>
  </div>
  <div class="spec abs">
    <h4>Caravan type<br>Guide</h4>
    <ul>
      <li><svg width="12" height="12"><circle cx="6" cy="6" r="5" fill="#1f73b7"/></svg>Sleeps</li>
      <li><svg width="12" height="12"><circle cx="6" cy="6" r="5" fill="#1f73b7"/></svg>Bedrooms</li>
      <li><svg width="12" height="12"><circle cx="6" cy="6" r="5" fill="#1f73b7"/></svg>Bathrooms</li>
      <li><svg width="12" height="12"><circle cx="6" cy="6" r="5" fill="#1f73b7"/></svg>Check in</li>
      <li><svg width="12" height="12"><circle cx="6" cy="6" r="5" fill="#1f73b7"/></svg>Check out</li>
      <li><svg width="12" height="12"><circle cx="6" cy="6" r="5" fill="#1f73b7"/></svg>Smoking allowed</li>
      <li><svg width="12" height="12"><circle cx="6" cy="6" r="5" fill="#1f73b7"/></svg>Disabled facilities</li>
      <li><svg width="12" height="12"><circle cx="6" cy="6" r="5" fill="#1f73b7"/></svg>Pets allowed</li>
      <li><svg width="12" height="12"><circle cx="6" cy="6" r="5" fill="#1f73b7"/></svg>Linen</li>
      <li><svg width="12" height="12"><circle cx="6" cy="6" r="5" fill="#1f73b7"/></svg>Company</li>
    </ul>
  </div>
  <div class="spec-values abs">
    <h4>Lodge<br>Luxury Lodge</h4>
    <ul>
      <li>6</li><li>3</li><li>2</li><li>3pm</li><li>10am</li><li>No</li><li>No</li><li>No</li><li>Included</li><li>Pinebrook Stays</li>
    </ul>
  </div>
</section>

<section class="booking panel abs">
  <div class="sec-head">Booking Information</div>
  <div class="pay-box"><span></span>DirectPay</div>
  <p>If you would like to book a holiday which is more than 3 months away you can spread the cost with our <a>Monthly or Weekly Payment Plan</a>.</p>
  <p>If the holiday is less than 8 weeks away full payment via credit card, debit card or bank transfer is required at the time of booking.</p>
  <p>With Monthly you can pay a £50 deposit to secure your date with the final balance due 8 weeks before your holiday. If you prefer you can make a single payment in full.</p>
  <p><strong>Final Balance Due</strong><br>This is due at least 8 weeks before your holiday.</p>
  <p><strong>Non Refundable Deposit</strong><br>The £50 deposit secures your date so we can reserve the lodge. If you cancel, this payment is non-refundable.</p>
  <p><strong>Security Bond</strong><br>We require a security bond payment of £100 prior to your holiday. We expect the lodge to be left in the same condition as when you arrived. Should there be any damage or additional cleaning needed, we reserve the right to keep your deposit. Otherwise it is returned within 14 days of your departure date.</p>
  <p><strong>Park Passes</strong><br><a>Click here for the park passes</a> Please remember to collect passes from reception on arrival. Passes are only available from the reception desk and must be worn at all times on the park.</p>
</section>

<aside class="availability abs">
  <div class="side-head">Availability</div>
  <p>To make a booking select the price below of your chosen stay. If you are looking for a 7 day booking you can select 7 days on the next page from the dropdown.</p>
  <div class="tabs"><div>2015</div><div class="on">2016</div></div>
  <ul class="dates">
    <li><span>Fri 04 September</span><b>£269.00</b></li>
    <li><span>Mon 07 September</span><b>£249.00</b></li>
    <li><span>Fri 11 September</span><b>£269.00</b></li>
    <li><span>Mon 14 September</span><b>£249.00</b></li>
    <li><span>Fri 18 September</span><b>£269.00</b></li>
    <li><span>Mon 21 September</span><b>£229.00</b></li>
    <li><span>Fri 25 September</span><b>£249.00</b></li>
    <li><span>Mon 28 September</span><b>£229.00</b></li>
    <li><span>Fri 02 October</span><b>£249.00</b></li>
    <li><span>Mon 05 October</span><b>£229.00</b></li>
    <li><span>Fri 09 October</span><b>£249.00</b></li>
    <li><span>Mon 12 October</span><b>£229.00</b></li>
    <li><span>Fri 16 October</span><b>£249.00</b></li>
    <li><span>Mon 19 October</span><b>£299.00</b></li>
    <li><span>Fri 23 October</span><b>£349.00</b></li>
    <li class="dark"><span>Mon 26 October</span><b>£299.00</b></li>
    <li class="dark"><span>Fri 30 October</span><b>£229.00</b></li>
    <li class="dark"><span>Mon 02 November</span><b>£199.00</b></li>
    <li class="dark"><span>Fri 06 November</span><b>£219.00</b></li>
    <li class="dark"><span>Mon 09 November</span><b>£199.00</b></li>
    <li class="dark"><span>Fri 13 November</span><b>£219.00</b></li>
    <li class="dark"><span>Mon 16 November</span><b>£199.00</b></li>
    <li class="dark"><span>Fri 20 November</span><b>£219.00</b></li>
    <li class="dark"><span>Mon 23 November</span><b>£199.00</b></li>
    <li class="dark"><span>Fri 27 November</span><b>£219.00</b></li>
    <li class="dark"><span>Mon 30 November</span><b>£199.00</b></li>
    <li class="dark"><span>Fri 04 December</span><b>£229.00</b></li>
  </ul>
</aside>

<aside class="reviews panel abs">
  <div class="side-head">Latest Reviews</div>
  <h5>Hannah Carlow</h5>
  <em>Stayed in Ashford Lodge</em>
  <p>Very clean on arrival, lovely quiet location with fantastic views over the lake. We all had an amazing time, having a wedding reunion and a short stay too.</p>
</aside>

<section class="features abs">
  <h2>FEATURES</h2>
  <div class="feat-cols">
    <ul>
      <li><svg width="12" height="12"><path d="M1 6l3 3 7-7" stroke="#8cb83c" stroke-width="2" fill="none"/></svg>2 Showers</li>
      <li><svg width="12" height="12"><path d="M1 6l3 3 7-7" stroke="#8cb83c" stroke-width="2" fill="none"/></svg>40 Inch TV</li>
      <li><svg width="12" height="12"><path d="M1 6l3 3 7-7" stroke="#8cb83c" stroke-width="2" fill="none"/></svg>Central Heating</li>
      <li><svg width="12" height="12"><path d="M1 6l3 3 7-7" stroke="#8cb83c" stroke-width="2" fill="none"/></svg>Double Glazing</li>
      <li><svg width="12" height="12"><path d="M1 6l3 3 7-7" stroke="#8cb83c" stroke-width="2" fill="none"/></svg>DVD player</li>
      <li><svg width="12" height="12"><path d="M1 6l3 3 7-7" stroke="#8cb83c" stroke-width="2" fill="none"/></svg>Fridge Freezer</li>
      <li><svg width="12" height="12"><path d="M1 6l3 3 7-7" stroke="#8cb83c" stroke-width="2" fill="none"/></svg>Garden table and chairs</li>
      <li><svg width="12" height="12"><path d="M1 6l3 3 7-7" stroke="#8cb83c" stroke-width="2" fill="none"/></svg>Hoover</li>
      <li><svg width="12" height="12"><path d="M1 6l3 3 7-7" stroke="#8cb83c" stroke-width="2" fill="none"/></svg>Microwave</li>
    </ul>
    <ul>
      <li><svg width="12" height="12"><path d="M1 6l3 3 7-7" stroke="#8cb83c" stroke-width="2" fill="none"/></svg>Private Parking</li>
      <li><svg width="12" height="12"><path d="M1 6l3 3 7-7" stroke="#8cb83c" stroke-width="2" fill="none"/></svg>Shower</li>
      <li><svg width="12" height="12"><path d="M1 6l3 3 7-7" stroke="#8cb83c" stroke-width="2" fill="none"/></svg>TV with Digital Channels</li>
      <li><svg width="12" height="12"><path d="M1 6l3 3 7-7" stroke="#8cb83c" stroke-width="2" fill="none"/></svg>2 Toilets</li>
      <li><svg width="12" height="12"><path d="M1 6l3 3 7-7" stroke="#8cb83c" stroke-width="2" fill="none"/></svg>Blu Ray Player</li>
      <li><svg width="12" height="12"><path d="M1 6l3 3 7-7" stroke="#8cb83c" stroke-width="2" fill="none"/></svg>Dish Washer</li>
      <li><svg width="12" height="12"><path d="M1 6l3 3 7-7" stroke="#8cb83c" stroke-width="2" fill="none"/></svg>Duvets and Pillows provided</li>
      <li><svg width="12" height="12"><path d="M1 6l3 3 7-7" stroke="#8cb83c" stroke-width="2" fill="none"/></svg>Freestanding sofa and chairs</li>
      <li><svg width="12" height="12"><path d="M1 6l3 3 7-7" stroke="#8cb83c" stroke-width="2" fill="none"/></svg>Front and Side Decking</li>
    </ul>
    <ul>
      <li><svg width="12" height="12"><path d="M1 6l3 3 7-7" stroke="#8cb83c" stroke-width="2" fill="none"/></svg>Gas and Electric included in price</li>
      <li><svg width="12" height="12"><path d="M1 6l3 3 7-7" stroke="#8cb83c" stroke-width="2" fill="none"/></svg>Iron</li>
      <li><svg width="12" height="12"><path d="M1 6l3 3 7-7" stroke="#8cb83c" stroke-width="2" fill="none"/></svg>Oven</li>
      <li><svg width="12" height="12"><path d="M1 6l3 3 7-7" stroke="#8cb83c" stroke-width="2" fill="none"/></svg>Selection of Pots, Pans and Cutlery</li>
      <li><svg width="12" height="12"><path d="M1 6l3 3 7-7" stroke="#8cb83c" stroke-width="2" fill="none"/></svg>Toaster</li>
      <li><svg width="12" height="12"><path d="M1 6l3 3 7-7" stroke="#8cb83c" stroke-width="2" fill="none"/></svg>Washing Machine</li>
    </ul>
  </div>
</section>

<section class="cards abs">
  <div class="card-photo" role="img" aria-label="Ashford lodge lounge"></div>
  <div class="card-text">
    <h3>Ashford</h3>
    <p>Spacious family lodge with three bedrooms and a large sunny deck.</p>
    <span class="card-btn">VIEW</span>
    <div class="stars"><svg width="70" height="12"><g fill="#8cb83c"><circle cx="6" cy="6" r="5"/><circle cx="20" cy="6" r="5"/><circle cx="34" cy="6" r="5"/><circle cx="48" cy="6" r="5"/><circle cx="62" cy="6" r="5"/></g></svg></div>
  </div>
  <div class="card-photo" role="img" aria-label="Kendal caravan interior"></div>
  <div class="card-text">
    <h3>The Kendal</h3>
    <p>Bright modern caravan close to the lake and play area.</p>
    <span class="card-btn">VIEW</span>
    <div class="stars"><svg width="70" height="12"><g fill="#8cb83c"><circle cx="6" cy="6" r="5"/><circle cx="20" cy="6" r="5"/><circle cx="34" cy="6" r="5"/><circle cx="48" cy="6" r="5"/><circle cx="62" cy="6" r="5"/></g></svg></div>
  </div>
  <div class="card-text">
    <h3>The Hartley</h3>
    <p>Cosy two bedroom caravan ideal for couples and small families.</p>
    <span class="card-btn">VIEW</span>
    <div class="stars"><svg width="70" height="12"><g fill="#8cb83c"><circle cx="6" cy="6" r="5"/><circle cx="20" cy="6" r="5"/><circle cx="34" cy="6" r="5"/><circle cx="48" cy="6" r="5"/><circle cx="62" cy="6" r="5"/></g></svg></div>
  </div>
  <div class="card-photo" role="img" aria-label="Hartley caravan lounge"></div>
  <div class="card-text">
    <h3>The Bramwell</h3>
    <p>Luxury caravan with open-plan living and woodland views.</p>
    <span class="card-btn">VIEW</span>
    <div class="stars"><svg width="70" height="12"><g fill="#8cb83c"><circle cx="6" cy="6" r="5"/><circle cx="20" cy="6" r="5"/><circle cx="34" cy="6" r="5"/><circle cx="48" cy="6" r="5"/><circle cx="62" cy="6" r="5"/></g></svg></div>
  </div>
  <div class="card-photo" role="img" aria-label="Bramwell caravan dining area"></div>
</section>
<div class="view-all abs">View All</div>

<footer class="site-footer abs">
  <div class="foot-col abs" style="left:160px;width:260px">
    <h4>Newsletter Signup</h4>
    <p>Join our mailing list to receive late deals and news about our lodges.</p>
    <div class="input"></div>
    <div class="subscribe">Subscribe</div>
  </div>
  <div class="foot-col abs" style="left:480px;width:260px">
    <h4>Contact Information</h4>
    <p>Contact our friendly team to book your stay or ask about availability at any of our lodges and caravans.</p>
    <p>T: 0800 555 0142<br>E: hello@pinebrookstays.com<br>www.pinebrookstays.com</p>
  </div>
  <div class="foot-col abs" style="left:800px;width:260px">
    <h4>Sitemap</h4>
    <div class="sitemap">
      <span>Home</span><span>Reviews</span>
      <span>Beds</span><span>Privacy Policy</span>
      <span>Blog</span><span>Booking Terms</span>
      <span>Lodges</span><span>News</span>
      <span>Late Deals</span><span>FAQs</span>
      <span>Local Area</span><span>Sitemap</span>
    </div>
  </div>
</footer>
<div class="bottom-bar abs">
  <span class="copy">Design © 2015 Pinebrook Stays. All Rights Reserved.</span>
  <div class="social"><span>Social Icons</span><i></i><i></i><i></i><i></i><i></i></div>
</div>

</body>
</html>
```